Vantiqo custom business card design

Need a authentic, innovative business card design for a new mobile app business. I am uploading a few screen images from our app for you to view. I would like app design theme to match business card design. I can also send logo images.

```html
<!DOCTYPE html>
<html lang="en">
<head>
<meta charset="utf-8">
<title>Vantiqo business card</title>
<link rel="stylesheet" href="https://fonts.googleapis.com/css2?family=Open+Sans:wght@400;600;700;800&display=swap">
<style>
  :root {
    --bg: #3a3b3d;
    --card: #ffffff;
    --purple: #5c0f8b;
    --purple-deep: #4a0a73;
    --ink: #1b1b1b;
    --text: #3d3d3d;
    --lavender: #e6dcef;
    --grey-soft: #e3e3e3;
  }
  * { box-sizing: border-box; margin: 0; padding: 0; }
  html, body { width: 1200px; height: 1000px; overflow: hidden; }
  body {
    background: var(--bg);
    font-family: "Open Sans", Arial, sans-serif;
    display: flex;
    flex-direction: column;
    align-items: center;
    justify-content: center;
    gap: 44px;
  }
  .card {
    position: relative;
    width: 760px;
    height: 434px;
    background: var(--card);
    overflow: hidden;
  }

  /* Back side */
  .card-back .pattern {
    position: absolute;
    inset: 0;
    background: linear-gradient(135deg, var(--lavender) 0%, var(--grey-soft) 50%, var(--lavender) 100%);
    opacity: 0.75;
  }
  .card-back .signoff {
    position: absolute;
    right: 34px;
    bottom: 40px;
    text-align: right;
  }
  .brand-mark {
    display: inline-flex;
    align-items: center;
    gap: 8px;
    font-weight: 800;
    color: var(--ink);
  }
  .brand-mark .dot {
    border-radius: 50%;
    background: var(--purple);
  }
  .card-back .brand-mark { font-size: 26px; }
  .card-back .brand-mark .dot { width: 18px; height: 18px; }
  .card-back .site {
    margin-top: 6px;
    font-size: 17px;
    color: var(--text);
  }

  /* Front side */
  .card-front .brand-mark {
    position: absolute;
    top: 96px;
    right: 58px;
    font-size: 50px;
    letter-spacing: -0.5px;
  }
  .card-front .brand-mark .dot { width: 34px; height: 34px; }
  .contact {
    position: absolute;
    left: 52px;
    top: 150px;
    color: var(--text);
  }
  .contact .name {
    font-size: 30px;
    font-weight: 700;
    color: var(--purple);
    line-height: 1.1;
  }
  .contact .role {
    font-size: 18px;
    text-transform: uppercase;
    margin-bottom: 14px;
  }
  .contact p {
    font-size: 18px;
    line-height: 1.45;
  }
  .contact b { color: var(--purple); font-weight: 700; }
  .band {
    position: absolute;
    left: 0;
    right: 0;
    bottom: 0;
    height: 78px;
    display: flex;
  }
  .band .fill {
    flex: 1;
    background: linear-gradient(90deg, var(--purple) 0%, var(--purple-deep) 100%);
    color: #fff;
    font-size: 20px;
    letter-spacing: 7px;
    padding: 22px 0 0 52px;
  }
  .band .end {
    width: 130px;
    background: var(--ink);
  }
</style>
</head>
<body>
  <section class="card card-back" aria-label="Card back">
    <div class="pattern" role="img" aria-label="Faint repeating brand pattern in lavender and grey"></div>
    <div class="signoff">
      <div class="brand-mark"><span class="dot"></span>Vantiqo</div>
      <div class="site">www.vantiqo.com</div>
    </div>
  </section>

  <section class="card card-front" aria-label="Card front">
    <div class="brand-mark"><span class="dot"></span>Vantiqo</div>
    <div class="contact">
      <h1 class="name">MARLA QUINT</h1>
      <div class="role">President</div>
      <p>2710 Harwell Lane Oak Ridge, NY 11920</p>
      <p><b>P:</b> 555 0142 7781 <b>M:</b> 555 0193 4460</p>
      <p><b>F:</b> 555 0127 3398 <b>E:</b> marla@vantiqo.com</p>
    </div>
    <div class="band">
      <div class="fill">www.vantiqo.com</div>
      <div class="end"></div>
    </div>
  </section>
</body>
</html>
```